Event Website for the Audio & Visual Industry

Convene is an exhibition aimed at meeting the business needs of audio and visual professionals – the visitors are the ones that make purchase decisions when buying anything to do with AV installation, Lighting & Entertainment Technology, DJ Technologies and even Musical Instruments.

We need to rebuild our website to reflect the professional look but with a bit of creativity/flare that is associated with the industry.

Websites whose design is along the lines we're looking for:

• http:www.pelmora.com.au
• http:www.kavrin.com
• http://www.brightpanelfair.net/ (competitor expo, like the layout. Not fantastic though, but the best I’ve seen from the industry)
• http://www.tuvelo.com.au and http://www.ostrand.com.au/ (Like these brand websites, they are clean and corporate but the use of imagery allows it to have some personality)

Target Market(s)

Corporate AV End Users, Lighting Designers, Concert/Entertainment companies, Sound Engineers

Industry/Entity Type

Business

Requirements
Must have
• Refer to the current splash page – www.convene-expo.com
This is the look and feel we have developed for our brochure. We want to expand on this and create a professional corporate look and feel without alienating existing sound, light and vision sectors.

The website's focus is to register visitors to attend the show. Please include a floating 'Register Free' Call to action. Please also include floating social media buttons. For what I mean by 'floating' check out the Social media buttons on this website: http://quorvix.com/2012/02/19/tall-boat-preview/ (scroll down to see effect).

We'll like to include a Rotating Banner at the top.

Sponsor element at the bottom off the page.

Sign up form functionality

Menu to be: About the Show, What's On, Register, How to Exhibit, Blog, Contact us.

I would like to see designs for a content page as well as the homepage.

```html
<!DOCTYPE html>
<html lang="en">
<head>
<meta charset="utf-8">
<title>Convene 2012 – Sound, Light, Vision</title>
<link href="https://fonts.googleapis.com/css2?family=Barlow:wght@400;500;600&family=Barlow+Semi+Condensed:wght@500;600&display=swap" rel="stylesheet">
<style>
:root{
  --red:#c8102e;
  --red-soft:#d03a4f;
  --ink:#1c1c1c;
  --nav:#1f1f1f;
  --page:#e7e8ea;
  --white:#ffffff;
  --grey:#9a9a9a;
  --band-top:#555;
  --band-bot:#1e1e1e;
  --rule:#d6d6d6;
  --icon:#777;
}
*{margin:0;padding:0;box-sizing:border-box}
html,body{width:1200px;height:1148px;overflow:hidden}
body{background:var(--page);font-family:"Barlow",Arial,sans-serif;color:var(--ink);position:relative}
.abs{position:absolute}
.column{left:147px;width:909px;background:var(--white)}
.header{top:11px;height:198px}
.brand{left:35px;top:78px;font-size:44px;font-weight:500;letter-spacing:-1px;color:var(--ink);display:flex;align-items:center;gap:10px}
.brand .dot{width:14px;height:14px;border-radius:50%;background:var(--red)}
.brand small{font-size:14px;font-weight:400;letter-spacing:0;color:#333;align-self:flex-end;margin-bottom:6px}
.register-free{left:735px;top:0;width:174px;height:53px;background:var(--red);color:var(--white);font:600 19px "Barlow Semi Condensed",sans-serif;letter-spacing:.5px;display:flex;align-items:center;justify-content:center}
.dates{right:37px;top:83px;text-align:right}
.dates .when{font:500 33px "Barlow Semi Condensed",sans-serif;color:var(--red-soft)}
.dates .venue{font:600 14px "Barlow",sans-serif;color:#333;margin-top:2px}
.dates .place{font:600 14px "Barlow",sans-serif;color:var(--grey)}
.nav{left:147px;top:209px;width:909px;height:54px;background:var(--nav);display:flex}
.nav a{color:var(--white);text-decoration:none;font:600 11.5px "Barlow",sans-serif;letter-spacing:2px;display:flex;align-items:center;justify-content:center;border-right:1px solid #3a3a3a}
.nav a:last-child{border-right:0}
.band{left:0;top:279px;width:1200px;height:313px;background:linear-gradient(var(--band-top),var(--band-bot));border-top:2px solid #2b8fb0}
.hero{left:138px;top:269px;width:744px;height:312px;background:linear-gradient(135deg,#6a6570,#3a3538 55%,#8a8888)}
.hero-caption{left:138px;top:480px;width:450px;height:84px;background:rgba(0,0,0,.72);color:var(--white);font-size:26px;line-height:28px;padding:12px 0 0 36px}
.hero-caption span{color:#e8243c;font-size:19px}
.tabs{left:882px;top:269px;width:183px;height:312px;display:flex;flex-direction:column}
.tabs div{flex:1;background:linear-gradient(var(--white),#e2e2e2);border-bottom:1px solid #cfcfcf;display:flex;align-items:center;padding-left:21px;font:600 13px "Barlow",sans-serif;color:#222}
.tabs .on{color:var(--red);border-left:7px solid var(--red);padding-left:16px}
.float-cta{left:0;top:297px;width:81px}
.float-cta .mark{height:68px;background:var(--white);display:flex;align-items:center;justify-content:center;gap:4px;font-size:15px;font-weight:500}
.float-cta .mark i{width:6px;height:6px;border-radius:50%;background:var(--red)}
.float-cta .btn{height:48px;background:var(--red);color:var(--white);font:600 14px/14px "Barlow Semi Condensed",sans-serif;padding:10px 0 0 10px}
.body-card{top:581px;height:359px}
.tile{top:618px;height:166px}
.tile .photo{width:100%;height:130px}
.tile .label{height:36px;background:#111;color:var(--white);font:600 14.5px "Barlow",sans-serif;letter-spacing:.3px;display:flex;align-items:center;padding-left:12px}
.col-title{font:500 17px "Barlow Semi Condensed",sans-serif;color:var(--red);letter-spacing:.3px}
.col-text{font-size:13px;line-height:16px;margin-top:8px;color:#111}
.more{font-size:12.5px;color:var(--red);margin-top:8px}
.vrule{width:1px;height:95px;background:var(--rule);top:814px}
.email{left:466px;top:880px;width:196px;height:29px;border:1px solid #ccc;border-radius:3px;font-size:11px;color:#aaa;padding:7px 10px}
.submit{left:668px;top:880px;width:65px;height:29px;border:1px solid #ccc;border-radius:3px;font:600 13px "Barlow",sans-serif;display:flex;align-items:center;justify-content:center;background:linear-gradient(#fff,#ececec)}
.action{left:765px;width:261px;height:40px;border:1px solid #ccc;border-radius:2px;background:linear-gradient(#fff,#eee);display:flex;align-items:center;gap:12px;padding-left:18px;font:500 13px "Barlow",sans-serif;letter-spacing:1px;white-space:nowrap}
.action.tight{letter-spacing:.4px;gap:10px;padding-left:16px}
.sponsors{left:147px;top:940px;width:909px;height:109px;background:#1e1e1e}
.sponsors .title{left:34px;top:44px;font:600 17px "Barlow Semi Condensed",sans-serif;color:#7a7a7a}
.sponsor{top:40px;color:var(--white);font:600 22px "Barlow",sans-serif;display:flex;align-items:center;gap:8px}
.sponsor i{width:10px;height:10px;background:var(--red)}
.footer{top:1049px;height:99px}
.legal{left:17px;top:18px;font-size:9.5px;line-height:15px;color:#333}
.by{right:30px;top:20px;text-align:left;font-size:9.5px;color:#111}
.by b{display:block;font:600 22px "Barlow",sans-serif;color:#aaa;margin-top:4px}
</style>
</head>
<body>
  <section class="abs column header">
    <div class="abs brand"><span class="dot"></span>Convene<small>2012 · sound.light.vision</small></div>
    <a class="abs register-free">REGISTER FREE</a>
    <div class="abs dates">
      <div class="when">21st-23rd AUGUST 2012</div>
      <div class="venue">HARBOURSIDE CONVENTION &amp; EXHIBITION CENTRE</div>
      <div class="place">WATTLE QUAY, AUSTRALIA</div>
    </div>
  </section>

  <nav class="abs nav">
    <a style="width:208px">ABOUT THE SHOW</a>
    <a style="width:140px">WHAT'S ON</a>
    <a style="width:135px">REGISTER</a>
    <a style="width:180px">HOW TO EXHIBIT</a>
    <a style="width:103px">BLOG</a>
    <a style="width:143px">CONTACT US</a>
  </nav>

  <div class="abs band"></div>
  <div class="abs hero" role="img" aria-label="Audience seated at a keynote session on the show floor"></div>
  <div class="abs hero-caption">Attend keynote sessions from some of the industry leaders. <span>Learn More</span></div>
  <div class="abs tabs">
    <div>DISCOVER THE LATEST</div>
    <div class="on">FEATURED KEYNOTE</div>
    <div>NEW PRODUCTS</div>
    <div>NEW LOCATION</div>
  </div>

  <aside class="abs float-cta">
    <div class="mark"><i></i>Convene</div>
    <div class="btn">REGISTER<br>FOR FREE</div>
  </aside>

  <section class="abs column body-card"></section>

  <article class="abs tile" style="left:159px;width:287px">
    <div class="photo" role="img" aria-label="Studio monitors and a digital mixing console" style="background:linear-gradient(135deg,#2a3a6a,#7d86b8 60%,#c9cbe0)"></div>
    <div class="label">DISCOVER THE LATEST ADVANCEMENTS</div>
  </article>
  <article class="abs tile" style="left:453px;width:292px">
    <div class="photo" role="img" aria-label="Exhibitor stand with a wall of video screens" style="background:linear-gradient(160deg,#151515,#3c3c44 55%,#8a8fa0)"></div>
    <div class="label">TALK TO INDUSTRY PROFESSIONALS</div>
  </article>
  <article class="abs tile" style="left:752px;width:293px">
    <div class="photo" role="img" aria-label="Audience attending an industry keynote" style="background:linear-gradient(135deg,#4a4448,#7a7478 60%,#b0acae)"></div>
    <div class="label" style="padding-left:18px">ATTEND INDUSTRY KEYNOTES</div>
  </article>

  <div class="abs" style="left:171px;top:812px;width:270px">
    <div class="col-title">FEATURED EXHIBITORS</div>
    <div class="col-text">Tuvelo, Ostrand, Kavrin, Marlow &amp; Finch, Vexa, Boardline, Mountis, Formatra, Halvorsen, Sonora-Tech, KRD, Brenna</div>
    <div class="more">AND MANY MORE...</div>
  </div>
  <div class="abs vrule" style="left:447px"></div>
  <div class="abs" style="left:467px;top:812px;width:270px">
    <div class="col-title">CONVENE NEWSLETTER</div>
    <div class="col-text" style="font-size:12.5px">Sign up for the newsletter and get year-round information source on Convene.</div>
  </div>
  <div class="abs email">enter your email</div>
  <div class="abs submit">submit</div>
  <div class="abs vrule" style="left:749px"></div>

  <div class="abs action" style="top:814px">
    <svg width="16" height="20" viewBox="0 0 16 20" aria-hidden="true"><path d="M1 1h9l5 5v13H1z" fill="#fff" stroke="var(--icon)" stroke-width="1.5"/><path d="M10 1v5h5" fill="none" stroke="var(--icon)" stroke-width="1.2"/><path d="M4 10h8M4 13h8M4 16h6" stroke="var(--icon)" stroke-width="1.2"/></svg>
    DOWNLOAD THE FLOORPLAN
  </div>
  <div class="abs action tight" style="top:868px">
    <svg width="30" height="18" viewBox="0 0 30 18" aria-hidden="true"><circle cx="8" cy="6" r="3.5" fill="#666"/><circle cx="22" cy="6" r="3.5" fill="#666"/><circle cx="15" cy="5" r="4" fill="#555"/><path d="M1 18c0-6 14-6 14 0zM15 18c0-6 14-6 14 0z" fill="#666"/><path d="M7 18c0-7 16-7 16 0z" fill="#555"/></svg>
    CONTACT THE CONVENE TEAM
  </div>

  <section class="abs sponsors">
    <div class="abs title">OUR SPONSORS</div>
    <div class="abs sponsor" style="left:250px"><i></i>Signalhall</div>
    <div class="abs sponsor" style="left:465px"><i></i>Meridale</div>
    <div class="abs sponsor" style="left:690px"><i></i>Convene</div>
  </section>

  <footer class="abs column footer">
    <div class="abs legal">
      STRICTLY TRADE ONLY. Entry is restricted to members of the ICT, Audio Visual and Entertainment industries.<br>
      Persons not in these categories, including children will not be admitted at any time.<br>
      © 2012 Meridale Exhibitions Australia. All rights reserved. Level 3, 58 Corran Street, Eastvale, NSW 2999, Australia.<br>
      Telephone: +61 9000 1234. Facsimile: +61 2 9000 5678.
    </div>
    <div class="abs by">Brought to you by<b>Meridale</b></div>
  </footer>
</body>
</html>
```